Orvenna Capital LLC

Need Professional Business cards for New Investment Fund

Target Market(s)

High Quality investors

Industry/Entity Type

Financial

Contact Information for Business Card

Phone Number +1 555 284 6190
Name Lukas Varenko
Title Fund Manager
email lv@FundOrvenna.com
Website www.FundOrvenna.com

Colors

Designer to choose colors to be used in the design.

Requirements
Must have
• Must have our Logo and all of the above. Must be made so lettering and loge can be raised

```html
<!DOCTYPE html>
<html lang="en">
<head>
<meta charset="utf-8">
<title>Orvenna Capital LLC – Business Cards</title>
<link rel="stylesheet" href="https://fonts.googleapis.com/css2?family=Roboto:wght@400;500;700&display=swap">
<style>
  :root {
    --backdrop: #bdbdbb;
    --card-dark: #39433b;
    --card-light: #f3f3f1;
    --ink-dark: #3a433c;
    --ink-body: #4a4f4b;
    --accent: #8cbf1f;
    --emboss: #7f8781;
  }
  * { margin: 0; padding: 0; box-sizing: border-box; }
  html, body {
    width: 1200px; height: 1138px; overflow: hidden;
    background: var(--backdrop);
    font-family: "Roboto", sans-serif;
  }
  .canvas { position: relative; width: 1200px; height: 1138px; }
  .card {
    position: absolute; left: 274px; width: 622px; height: 374px;
    border-radius: 16px; overflow: hidden;
  }
  .card-front { top: 186px; background: var(--card-dark); }
  .card-back { top: 608px; background: var(--card-light); }

  .front-wordmark {
    position: absolute; left: 0; right: 0; top: 164px;
    text-align: center;
    font-size: 62px; line-height: 62px; font-weight: 500; letter-spacing: 2px;
    color: var(--emboss);
    text-transform: uppercase;
  }

  .back-wordmark {
    position: absolute; left: 28px; top: 78px;
    display: flex; align-items: center; gap: 10px;
    font-size: 34px; line-height: 40px; font-weight: 500; letter-spacing: 1px;
    color: var(--ink-dark); text-transform: uppercase;
  }
  .back-wordmark .mark-square {
    width: 18px; height: 18px; background: var(--accent);
  }

  .holder-name {
    position: absolute; left: 28px; top: 196px;
    font-size: 24px; line-height: 30px; font-weight: 500; color: var(--ink-dark);
  }
  .holder-title {
    position: absolute; left: 28px; top: 236px;
    font-size: 16px; line-height: 20px; font-weight: 400; color: var(--ink-body);
  }
  .contact-list {
    position: absolute; left: 28px; top: 275px;
    list-style: none;
  }
  .contact-list li {
    display: flex; align-items: center;
    height: 23.5px;
    font-size: 16px; color: var(--ink-body);
  }
  .contact-list svg { width: 14px; height: 14px; margin-right: 18px; fill: var(--accent); }
</style>
</head>
<body>
<div class="canvas">
  <section class="card card-front" aria-label="Card front">
    <div class="front-wordmark">Orvenna</div>
  </section>

  <section class="card card-back" aria-label="Card back">
    <div class="back-wordmark"><span class="mark-square"></span>Orvenna</div>
    <div class="holder-name">Lukas Varenko</div>
    <div class="holder-title">Fund Manager</div>
    <ul class="contact-list">
      <li>
        <svg viewBox="0 0 16 16" aria-hidden="true"><path d="M1 5c0-2 3-3 7-3s7 1 7 3v1h-4V5H5v1H1z M3 8h10l1 6H2z"/></svg>
        +1 555 284 6190
      </li>
      <li>
        <svg viewBox="0 0 16 16" aria-hidden="true"><path d="M1 3h14v10H1z"/><path d="M1 3l7 6 7-6" fill="none" stroke="#f3f3f1" stroke-width="1.4"/></svg>
        lv@FundOrvenna.com
      </li>
      <li>
        <svg viewBox="0 0 16 16" aria-hidden="true"><circle cx="8" cy="8" r="7"/><path d="M1 8h14M8 1c-3 4-3 10 0 14M8 1c3 4 3 10 0 14" fill="none" stroke="#f3f3f1" stroke-width="1"/></svg>
        www.FundOrvenna.com
      </li>
    </ul>
  </section>
</div>
</body>
</html>
```